Corporate Business Card

Very professional, Modern, Not to busy, include phone address email, website
(253) 617-4930, 18761 52nd Avenue S, Kent, WA 98047, martin@plumlinegroup.com, varkoworks.com

Target Market(s)

Manufacturing

Industry/Entity Type

Aero, machining, manufacturing, Off road racing

Contact Information for Business Card

Phone, address email, website

```html
<!DOCTYPE html>
<html lang="en">
<head>
<meta charset="utf-8">
<title>Varko Works – Business Card</title>
<link href="https://fonts.googleapis.com/css2?family=Open+Sans:wght@400;700&display=swap" rel="stylesheet">
<style>
  :root{
    --bg:#858584;
    --navy:#1f3368;
    --navy-deep:#18285a;
    --red:#d9262c;
    --white:#ffffff;
    --ink:#4a4a4a;
    --rule:#2b3f78;
  }
  *{box-sizing:border-box;margin:0;padding:0}
  html,body{width:1200px;height:801px;overflow:hidden}
  body{
    background:var(--bg);
    font-family:"Open Sans",Arial,sans-serif;
    position:relative;
  }
  .card{
    position:absolute;
    top:252px;
    width:525px;
    height:300px;
    box-shadow:0 6px 18px rgba(0,0,0,.25);
    overflow:hidden;
  }
  /* front */
  .card-front{left:45px;background:var(--white)}
  .card-front .edge-band{
    position:absolute;left:0;bottom:0;width:100%;height:10px;
  }
  .brand{
    position:absolute;left:40px;top:112px;width:220px;
  }
  .brand-name{
    font-weight:700;font-size:34px;line-height:1;color:var(--navy);
    letter-spacing:.5px;white-space:nowrap;
  }
  .brand-rule{
    margin-top:16px;height:2px;width:190px;background:var(--navy);
  }
  .divider{
    position:absolute;left:285px;top:88px;width:1px;height:112px;background:var(--rule);
  }
  .contact{
    position:absolute;left:305px;top:82px;
    list-style:none;font-size:13.5px;line-height:24px;color:var(--ink);
  }
  .contact li{display:flex;align-items:center;gap:7px;white-space:nowrap}
  .contact .plain{padding-left:0}
  .contact svg{width:11px;height:11px;fill:var(--red);flex:none}
  /* back */
  .card-back{
    left:630px;background:var(--navy);
    border-bottom:2px solid var(--red);
  }
  .back-brand{
    position:absolute;left:0;right:0;top:112px;text-align:center;
  }
  .back-brand .brand-name{color:var(--navy-deep);font-size:46px}
  .back-brand .brand-rule{
    margin:18px auto 0;width:250px;background:var(--navy-deep);
  }
</style>
</head>
<body>

<section class="card card-front" aria-label="Card front">
  <svg class="edge-band" viewBox="0 0 525 10" preserveAspectRatio="none" aria-hidden="true">
    <rect x="0" y="0" width="525" height="10" fill="#1f3368"/>
    <polygon points="215,0 525,0 525,10 205,10" fill="#d9262c"/>
  </svg>

  <div class="brand">
    <div class="brand-name">Varko Works</div>
    <div class="brand-rule"></div>
  </div>

  <div class="divider"></div>

  <ul class="contact">
    <li class="plain">18761 52nd Avenue S</li>
    <li class="plain">Kent, WA 98047</li>
    <li>
      <svg viewBox="0 0 24 24" aria-hidden="true"><path d="M6.6 10.8a15.1 15.1 0 0 0 6.6 6.6l2.2-2.2a1 1 0 0 1 1-.25 11.4 11.4 0 0 0 3.6.57 1 1 0 0 1 1 1V20a1 1 0 0 1-1 1A17 17 0 0 1 3 4a1 1 0 0 1 1-1h3.5a1 1 0 0 1 1 1c0 1.25.2 2.45.57 3.57a1 1 0 0 1-.25 1z"/></svg>
      (253) 617-4930
    </li>
    <li>
      <svg viewBox="0 0 24 24" aria-hidden="true"><path d="M2 5h20v14H2z M4 7v.5l8 5 8-5V7l-8 5z" fill-rule="evenodd"/></svg>
      martin@plumlinegroup.com
    </li>
    <li>
      <svg viewBox="0 0 24 24" aria-hidden="true"><path d="M12 2a10 10 0 1 0 0 20 10 10 0 0 0 0-20zm6.9 6h-3a15.7 15.7 0 0 0-1.3-3.9A8 8 0 0 1 18.9 8zM12 4c.8 1.2 1.5 2.5 1.9 4h-3.8c.4-1.5 1.1-2.8 1.9-4zM4.3 14a8 8 0 0 1 0-4h3.4a16 16 0 0 0 0 4zm.8 2h3a15.7 15.7 0 0 0 1.3 3.9A8 8 0 0 1 5.1 16zm3-8h-3a8 8 0 0 1 4.3-3.9C8.8 5.3 8.4 6.6 8.1 8zM12 20c-.8-1.2-1.5-2.5-1.9-4h3.8c-.4 1.5-1.1 2.8-1.9 4zm2.3-6H9.7a14.6 14.6 0 0 1 0-4h4.6a14.6 14.6 0 0 1 0 4zm.3 5.9c.6-1.2 1-2.5 1.3-3.9h3a8 8 0 0 1-4.3 3.9zm1.7-5.9a16 16 0 0 0 0-4h3.4a8 8 0 0 1 0 4z"/></svg>
      varkoworks.com
    </li>
  </ul>
</section>

<section class="card card-back" aria-label="Card back">
  <div class="back-brand">
    <div class="brand-name">Varko Works</div>
    <div class="brand-rule"></div>
  </div>
</section>

</body>
</html>
```